Maple Sprout Menu (Vegetarian Restaurant Concept)

Maple Sprout is a new concept fast casual restaurant
renders are attached so you can see the style of restaurant
Maple Sproute is a vibrant and modern Vegetarian fast casual restaurant concept that mixes fresh food, energy, great décor, and a comfortable, welcoming atmosphere to provide a memorable and all Vegetarian dining experience.
Our Mission is to be top of mind when consumers think Vegetarian food!
Updates
Need extra days to review
Target Market(s)
the menu is vegetarian and appeals to a broad demographic in USA
Font styles to use
Colors
Designer to choose colors to be used in the design.
Requirements
Must have
- well colored and well laid out menu - should not be cartoonish
Nice to have
- For Phots please use the shots in this file:
- https://www.filecrate-share.net/sh/qtrv8knw2lpa5zc/BBBxR_pLmNoQwEE4J_TKX_Va?dl=0
- note these are untouched and you are free to change as needed
Should not have
- Should not be cartoonish - nor kives, forks etc in the design

```html
<!DOCTYPE html>
<html lang="en">
<head>
<meta charset="utf-8">
<title>Maple Sproute Menu</title>
<link href="https://fonts.googleapis.com/css2?family=Josefin+Sans:wght@400;600;700&family=Quicksand:wght@400;500&display=swap" rel="stylesheet">
<style>
  :root {
    --paper: #ffffff;
    --leaf: #5b7f2a;
    --forest: #2f4a2a;
    --stone: #6b6b6b;
    --sprout: #7c9c4c;
    --rule: #9aa3a0;
    --carrot: #e8955a;
    --ink: #23272a;
  }
  * { box-sizing: border-box; margin: 0; padding: 0; }
  html, body { width: 729px; height: 1200px; overflow: hidden; background: var(--paper); }
  .menu { position: relative; width: 729px; height: 1200px; }
  .frame { position: absolute; left: 0; top: 0; }

  .column { position: absolute; }
  .column--left { left: 67px; width: 289px; }
  .column--right { left: 371px; width: 288px; }

  .section { position: absolute; left: 0; width: 100%; text-align: center; }
  .section-title {
    display: inline-block;
    font-family: "Josefin Sans", sans-serif;
    font-weight: 600;
    font-size: 18px;
    line-height: 21px;
    letter-spacing: 0.14em;
    color: var(--leaf);
    padding: 0 5px 3px 8px;
    border-bottom: 3px double var(--leaf);
    margin-bottom: 9px;
  }

  .item { padding: 8.5px 0 7px; border-bottom: 1px dotted var(--rule); }
  .item:last-child { border-bottom: none; }
  .item-name {
    font-family: "Josefin Sans", sans-serif;
    font-weight: 600;
    font-size: 13.5px;
    line-height: 17px;
    letter-spacing: 0.2em;
    color: var(--forest);
    white-space: nowrap;
  }
  .item-desc {
    font-family: "Quicksand", sans-serif;
    font-weight: 400;
    font-size: 11.5px;
    line-height: 16.5px;
    letter-spacing: 0.04em;
    color: var(--stone);
    margin-top: 6px;
    white-space: nowrap;
  }
  .item-price {
    font-family: "Quicksand", sans-serif;
    font-weight: 500;
    font-size: 11px;
    line-height: 18px;
    color: var(--sprout);
    margin-top: 6px;
  }
  .item-desc + .item-price { margin-top: 0; }

  .brand { position: absolute; left: 67px; width: 289px; top: 960px; text-align: center; }
  .brand-mark { display: block; margin: 0 auto 14px; width: 52px; height: 52px; border-radius: 50%; background: var(--carrot); }
  .brand-name {
    font-family: "Josefin Sans", sans-serif;
    font-weight: 700;
    font-size: 25px;
    line-height: 30px;
    color: var(--ink);
  }
  .tagline {
    position: absolute; left: 85px; width: 248px; top: 1141px; text-align: center;
    font-family: "Josefin Sans", sans-serif;
    font-weight: 400;
    font-size: 12.5px;
    line-height: 16.5px;
    letter-spacing: 0.08em;
    color: var(--leaf);
    white-space: nowrap;
  }
</style>
</head>
<body>
<main class="menu">
  <svg class="frame" width="729" height="1200" aria-hidden="true">
    <defs>
      <pattern id="wave-h" width="8" height="6" patternUnits="userSpaceOnUse">
        <path d="M0 3 Q2 0.5 4 3 T8 3" fill="none" stroke="#7c9c4c" stroke-width="0.8"/>
      </pattern>
      <pattern id="wave-v" width="6" height="8" patternUnits="userSpaceOnUse">
        <path d="M3 0 Q0.5 2 3 4 T3 8" fill="none" stroke="#7c9c4c" stroke-width="0.8"/>
      </pattern>
    </defs>
    <rect x="40" y="33" width="648" height="6" fill="url(#wave-h)"/>
    <rect x="37" y="36" width="6" height="1121" fill="url(#wave-v)"/>
    <rect x="685" y="36" width="6" height="1121" fill="url(#wave-v)"/>
    <rect x="40" y="1154" width="45" height="6" fill="url(#wave-h)"/>
    <rect x="333" y="1154" width="355" height="6" fill="url(#wave-h)"/>
  </svg>

  <div class="column column--left">
    <section class="section" style="top:69px">
      <h2 class="section-title">SALADS</h2>
      <div class="item">
        <div class="item-name">BRUSSEL SPROUT CAESAR</div>
        <div class="item-desc">little gem romaine, toasted torn bread,<br>parmigiano reggiano</div>
        <div class="item-price">5</div>
      </div>
      <div class="item">
        <div class="item-name">HEIRLOOM BEET SALAD</div>
        <div class="item-desc">shaved chioggia beet, roasted golden<br>beet, red quinoa, little gem, arugula, lemon<br>vinaigrette</div>
        <div class="item-price">5</div>
      </div>
      <div class="item">
        <div class="item-name">ZESTY BLACK BEAN &amp; CORN<br>SALAD IN LETTUCE CUPS</div>
        <div class="item-desc">black beans, avocado &amp; roasted corn<br>topped with feta crumbles in butter lettuce</div>
        <div class="item-price">5</div>
      </div>
      <div class="item">
        <div class="item-name">GREEN, RED AND WHITE</div>
        <div class="item-desc">spring leaves, cherry tomatoes, avocado,<br>roasted almond &amp; goat cheese</div>
        <div class="item-price">5</div>
      </div>
    </section>

    <section class="section" style="top:522px">
      <h2 class="section-title">TOASTS</h2>
      <div class="item">
        <div class="item-name">EVERYTHING AVOCADO TOAST</div>
        <div class="item-desc">avocado on whole grain toast with our<br>signature spice blend</div>
        <div class="item-price">5</div>
      </div>
      <div class="item">
        <div class="item-name">TOMATO &amp; BEET BRUSCHETTA</div>
        <div class="item-price">5</div>
      </div>
      <div class="item">
        <div class="item-name">VEGETABLE MELT ON GARLIC<br>TOAST</div>
        <div class="item-price">5</div>
      </div>
    </section>

    <section class="section" style="top:794px">
      <h2 class="section-title">SOUP</h2>
      <div class="item">
        <div class="item-name">BLACK BEAN CHOWDER</div>
        <div class="item-price">5</div>
      </div>
    </section>
  </div>

  <div class="brand">
    <span class="brand-mark"></span>
    <div class="brand-name">Maple Sproute</div>
  </div>
  <p class="tagline">‘reimagining the meat-free<br>dining experience’</p>

  <div class="column column--right">
    <section class="section" style="top:66px">
      <h2 class="section-title">BURGERS, WRAPS &amp;<br>SANDWICHES</h2>
      <div class="item">
        <div class="item-name">SWEET POTATO, BLACK<br>BEAN VEGGIE BURGERS WITH<br>CABBAGE-PEPITA SLAW</div>
        <div class="item-price">5</div>
      </div>
      <div class="item">
        <div class="item-name">ROASTED VEGGIE, ARUGULA &amp;<br>HUMMUS WRAPS</div>
        <div class="item-price">5</div>
      </div>
      <div class="item">
        <div class="item-name">GARDEN BURGER</div>
        <div class="item-price">5</div>
      </div>
      <div class="item">
        <div class="item-name">BEANS &amp; GREENS QUESADILLAS</div>
        <div class="item-desc">greens, Mexican cheese, beans &amp; avocado,<br>with salsa</div>
        <div class="item-price">5</div>
      </div>
      <div class="item">
        <div class="item-name">VEGGIE BURRITO</div>
        <div class="item-desc">greens, Mexican cheese, beans, brown rice,<br>roasted chili corn &amp; avocado, with ancho<br>chili salsa, wheat tortilla</div>
        <div class="item-price">5</div>
      </div>
    </section>

    <section class="section" style="top:561px">
      <h2 class="section-title">BOWLS</h2>
      <div class="item">
        <div class="item-name">ROASTED VEGETABLE, &amp; SPINACH<br>BOWL</div>
        <div class="item-price">5</div>
      </div>
      <div class="item">
        <div class="item-name">SUGAR SNAP PEA &amp; CARROT<br>SOBA NOODLES</div>
        <div class="item-price">5</div>
      </div>
      <div class="item">
        <div class="item-name">WHOLE GRAIN &amp; VEGETABLE<br>BUDDHA BOWL</div>
        <div class="item-price">5</div>
      </div>
      <div class="item">
        <div class="item-name">ORANGE &amp; PISTACHIO QUINOA</div>
        <div class="item-price">5</div>
      </div>
    </section>

    <section class="section" style="top:893px">
      <h2 class="section-title">DESSERT</h2>
      <div class="item">
        <div class="item-name">STRAWBERRY BALSAMIC ICE<br>CREAM SUNDAE</div>
        <div class="item-price">5</div>
      </div>
      <div class="item">
        <div class="item-name">EXOTIC FRUIT BOWL</div>
        <div class="item-price">5</div>
      </div>
      <div class="item">
        <div class="item-name">WHITE AND DARK OATMEAL<br>COOKIE</div>
        <div class="item-price">5</div>
      </div>
    </section>
  </div>
</main>
</body>
</html>
```